We need a new business card that reflects who we are. Professional, classy, modern, and service ori

We need a business card design for a window coverings design company in Kansas City called Bright Lane Interiors. We offer professional, modern, and high quality window covering products. We are looking to portray an image of a big, national franchise. We are a 5 location (with showrooms) business with 10 professional designers and 4 professional installers. These cards will be used with Thank you cards, given to realtors, and asked for referrals with.

Target Market(s)

Kansas City

Industry/Entity Type

Business

Contact Information for Business Card

We would like our card to look clean and simple on the front, featuring our logo and Marlow Fenwick's. Our designers' phone numbers and emails should be displayed as well as their title.

Font styles to use
Sans Serif

Colors

Designer to choose colors to be used in the design.

Requirements
Must have
• Front - Logos, name, phone number, email address
• Back - Showroom locations, social media? Appt date/time?
Nice to have
• I would like a clean and modern look (not contemporary. I like a white background, but I am open to ideas. Looking for a "National chain" look for a small business.
Should not have
• Too much busyness.

```html
<!DOCTYPE html>
<html lang="en">
<head>
<meta charset="utf-8">
<title>Bright Lane Interiors – Business Card</title>
<link href="https://fonts.googleapis.com/css2?family=Roboto:wght@400;500;700&family=Cormorant+Garamond:wght@500&display=swap" rel="stylesheet">
<style>
  :root {
    --backdrop: #2a2a2a;
    --card-grey: #8e9295;
    --card-white: #f3f3f3;
    --brand-red: #c8434a;
    --ink: #111111;
    --ink-grey: #555b60;
    --white: #ffffff;
    --partner-orange: #f08a24;
  }
  html, body {
    margin: 0;
    width: 1200px;
    height: 960px;
    overflow: hidden;
    background: var(--backdrop);
    font-family: "Roboto", Arial, sans-serif;
  }
  .canvas { position: relative; width: 1200px; height: 960px; }

  .card {
    position: absolute;
    width: 600px;
    height: 343px;
    box-shadow: 0 3px 8px rgba(0,0,0,.45);
  }
  .card--front { left: 314px; top: 113px; background: var(--card-grey); }
  .card--back { left: 311px; top: 472px; background: var(--card-white); }

  /* Front */
  .front-brand {
    position: absolute;
    left: 0; top: 123px;
    width: 294px; height: 104px;
    background: var(--white);
    display: flex;
    align-items: center;
    justify-content: center;
    gap: 10px;
  }
  .front-brand__mark { width: 20px; height: 20px; background: var(--brand-red); flex: none; }
  .front-brand__name {
    font-size: 25px;
    font-weight: 500;
    color: var(--ink);
    white-space: nowrap;
  }
  .contact { position: absolute; left: 324px; top: 119px; }
  .contact__name {
    margin: 0;
    font-size: 22px;
    font-weight: 500;
    color: var(--brand-red);
    letter-spacing: .3px;
    line-height: 1.1;
  }
  .contact__title {
    margin: 4px 0 12px;
    font-size: 15px;
    font-weight: 700;
    color: var(--ink);
    letter-spacing: .3px;
  }
  .contact__list { list-style: none; margin: 0; padding: 0; }
  .contact__item {
    display: flex; align-items: center; gap: 8px;
    font-size: 14.5px; color: var(--white); line-height: 19.5px;
  }
  .contact__icon { width: 13px; height: 13px; fill: var(--brand-red); flex: none; }

  /* Back */
  .back-brand {
    position: absolute; left: 60px; top: 90px; width: 250px;
    text-align: center;
  }
  .back-brand__name {
    display: inline-flex; align-items: center; gap: 8px;
    font-size: 21px; font-weight: 500; color: var(--ink); white-space: nowrap;
  }
  .back-brand__mark { width: 14px; height: 14px; background: var(--brand-red); }
  .back-brand__tagline {
    margin: 8px 0 0;
    font-family: "Cormorant Garamond", Georgia, serif;
    font-size: 13px; font-weight: 500; color: var(--ink); white-space: nowrap;
  }
  .showrooms { position: absolute; left: 340px; top: 41px; }
  .showrooms__heading {
    margin: 0; font-size: 14px; font-weight: 700; color: var(--brand-red); letter-spacing: .2px; line-height: 18px;
  }
  .showrooms__list { list-style: none; margin: 0; padding: 0; }
  .showrooms__list li {
    font-size: 14.5px; font-weight: 400; color: var(--ink-grey); line-height: 18px; letter-spacing: .3px;
  }
  .partner {
    display: flex; align-items: center; gap: 5px; margin-top: 6px;
    font-size: 12px; font-weight: 500; color: var(--ink-grey);
  }
  .partner__dot { width: 16px; height: 16px; border-radius: 50%; background: var(--partner-orange); }
  .social { display: flex; gap: 4px; margin-top: 9px; }
  .social span { width: 16px; height: 16px; border-radius: 50%; background: var(--brand-red); }

  .appointment { position: absolute; left: 43px; top: 233px; width: 510px; color: var(--brand-red); }
  .appointment__row { display: flex; align-items: baseline; font-size: 16px; margin-bottom: 22px; white-space: nowrap; }
  .appointment__line { border-bottom: 1px dotted #777; height: 0; margin: 0 4px 0 8px; }
  .appointment__suffix { font-size: 13px; }
</style>
</head>
<body>
<main class="canvas">

  <section class="card card--front" aria-label="Business card front">
    <div class="front-brand">
      <span class="front-brand__mark"></span>
      <span class="front-brand__name">Bright Lane Interiors</span>
    </div>
    <div class="contact">
      <h1 class="contact__name">EVAN HALE</h1>
      <p class="contact__title">DESIGNER</p>
      <ul class="contact__list">
        <li class="contact__item">
          <svg class="contact__icon" viewBox="0 0 16 16"><path d="M3.6 1l2.5 3-1.4 1.8c.9 2 2.5 3.6 4.5 4.5L11 8.9l3 2.5-1 3c-6.4 0-11.4-5-11.4-11.4z"/></svg>
          913.555.0142
        </li>
        <li class="contact__item">
          <svg class="contact__icon" viewBox="0 0 16 16"><path d="M1 3h14v1.2L8 9 1 4.2zM1 5.8l7 4.8 7-4.8V13H1z"/></svg>
          info@brightlaneinteriors.com
        </li>
        <li class="contact__item">
          <svg class="contact__icon" viewBox="0 0 16 16"><circle cx="8" cy="8" r="7"/><path d="M1 8h14M8 1c2.5 2.5 2.5 11.5 0 14M8 1c-2.5 2.5-2.5 11.5 0 14" stroke="#8e9295" stroke-width="1" fill="none"/></svg>
          brightlaneinteriors.com
        </li>
      </ul>
    </div>
  </section>

  <section class="card card--back" aria-label="Business card back">
    <div class="back-brand">
      <span class="back-brand__name"><span class="back-brand__mark"></span>Bright Lane Interiors</span>
      <p class="back-brand__tagline">Blinds, Shades, Shutters, Draperies &amp; Decor</p>
    </div>

    <div class="showrooms">
      <h2 class="showrooms__heading">SHOWROOM LOCATIONS</h2>
      <ul class="showrooms__list">
        <li>ASHDALE</li>
        <li>BRIARWOOD PARK</li>
        <li>KELL’S RIDGE</li>
        <li>EASTMOOR</li>
        <li>PINE HAVEN</li>
      </ul>
      <div class="partner"><span>Marlow Fenwick Gallery</span><span class="partner__dot"></span></div>
      <div class="social" aria-label="Social media"><span></span><span></span><span></span><span></span></div>
    </div>

    <div class="appointment">
      <div class="appointment__row">Name :<span class="appointment__line" style="width:432px"></span></div>
      <div class="appointment__row">Date :<span class="appointment__line" style="width:206px"></span>Time :<span class="appointment__line" style="width:134px"></span><span class="appointment__suffix">AM/PM</span></div>
    </div>
  </section>

</main>
</body>
</html>
```